MS Word Template for Proposals and RFP

Looking for a nice looking graphic template in MS Word. We will use this to make proposals and answer RFPs. Looking for something that will match our company brand, but give a fresh, up-to-date look and feel. There are a few pictures of a template I like. I don't necessarily like that logo - looks too "kid like" for business, but I really like how clean and organized it is. Most proposals and RFP responses are looooooonnnngggg and boring - need something that someone can look through and find what they are looking for quickly and easily.
Updates

Can't wait to see your designs!

Target Market(s)

School districts and other governmental employers

Industry/Entity Type

Business

Requirements
Must have
• Must include sample table of contents, section dividers, charts, graphs and tables that we customized based on the content. The goal is for it to look simple, clean, compelling - organized so it's easy to read, easy to find your way around - good headers, charts, flow charts, tables.... etc. Looking to have 5-10 template pages that we can use to put together and entire portfolio.
Should not have
• No "cutsie" comic sans/apple for the teacher kind of stuff - we are selling employee benefits to schools and other governmental entities. Should be more serious and conservative but also look compelling and draw in the reader.

```html
<!DOCTYPE html>
<html lang="en">
<head>
<meta charset="utf-8">
<title>Company Profile</title>
<link rel="stylesheet" href="https://fonts.googleapis.com/css2?family=Roboto:wght@400&display=swap">
<style>
  :root {
    --stage: #000000;
    --brand-blue: #6284c2;
    --brand-blue-deep: #4a70b9;
    --brand-blue-mid: #5679bd;
    --paper: #ffffff;
    --ink-light: #ffffff;
    --logo-blue: #4a72b8;
  }
  * { margin: 0; padding: 0; box-sizing: border-box; }
  html, body {
    width: 933px;
    height: 1200px;
    overflow: hidden;
    background: var(--stage);
  }
  .cover {
    position: absolute;
    left: 67px;
    top: 67px;
    width: 800px;
    height: 1067px;
    background: var(--brand-blue);
    font-family: "Roboto", sans-serif;
    color: var(--ink-light);
    overflow: hidden;
  }
  .cover-hero {
    position: absolute;
    left: 0;
    top: 0;
    width: 800px;
    height: 420px;
    background:
      radial-gradient(ellipse 70% 80% at 45% 30%, rgba(70, 108, 182, 0.9) 0%, rgba(70, 108, 182, 0) 75%),
      linear-gradient(to bottom, var(--brand-blue-deep) 0%, var(--brand-blue-mid) 45%, var(--brand-blue) 100%);
  }
  .cover-title {
    position: absolute;
    left: 0;
    top: 508px;
    width: 100%;
    text-align: center;
    font-size: 47px;
    font-weight: 400;
    line-height: 1.2;
  }
  .cover-subtitle {
    position: absolute;
    left: 0;
    top: 583px;
    width: 100%;
    text-align: center;
    font-size: 19.5px;
    font-weight: 400;
    line-height: 27px;
  }
  .brand-band {
    position: absolute;
    left: 0;
    top: 924px;
    width: 800px;
    height: 97px;
    background: var(--paper);
    display: flex;
    align-items: center;
    justify-content: center;
    gap: 14px;
  }
  .brand-mark {
    width: 16px;
    height: 16px;
    border-radius: 50%;
    background: var(--logo-blue);
  }
  .brand-name {
    font-size: 30px;
    font-weight: 400;
    letter-spacing: 1px;
    color: var(--logo-blue);
    text-transform: uppercase;
  }
</style>
</head>
<body>
  <main class="cover">
    <div class="cover-hero" role="img" aria-label="Faint national flag and country map illustration in blue tones"></div>
    <h1 class="cover-title">Company Profile</h1>
    <p class="cover-subtitle">Employee benefit solutions for school districts<br>and public employers across the nation</p>
    <footer class="brand-band">
      <span class="brand-mark"></span>
      <span class="brand-name">Meridian Benefit Partners</span>
    </footer>
  </main>
</body>
</html>
```